Motivational Poster Design Project

I would like to create a poster with some of my favorite quotes to hang in my office. I did a similar project in 2012 and I've uploaded the top 2 designs so you can get a better idea of what I'm looking for. I will provide feedback on your design within 24 hours of receiving it.

The poster must contain the following quotes:

"You’re only given a little spark of madness. You mustn’t lose it.”
- Dorian Fletcher

“The most contrarian thing of all is not to oppose the crowd but to think for yourself.”
- Marcus Olden

"I constantly see people rise in life who are not the smartest, sometimes not even the most diligent, but they are learning machines. They go to bed every night a little wiser than they were when they got up and boy does that help, particularly when you have a long run ahead of you."
- Frankie Dalgarth

“In theory, there’s no difference between theory and practice. But, in practice, there is.”
- Kees R. T. Ter Haverkamp

"At the end of the day, a reactionary life is a normal life. One thing is consistent in every remarkable person: they decide to do something remarkable. Don’t let the world choose who you become."
- Rohan Kapadia

“It usually takes 3-4 months to try enough that you can do a proper 80/20 analysis, then two months to design systems to scale what *is* working.”
-Ned Yarrow

“Authority is 20 percent given, 80 percent taken.”
- Glenn Mosbacker

“Your actions are consistent with the way the world occurs to you.”
- Dieter Kolbach

Project Deadline Extended
Reason: I am going to be travelling with no access to internet until January 5th, 2015. I am extending the project deadline until 12/31/14 and I'll make a final decision during the 1st week of January.

Target Market(s)

Personal Project

Industry/Entity Type

Learning

Requirements
Must have
• The poster will be 24" high x 36" long and printed on canvas, so the image you create needs to have a resolution of at least 2700 x 3900.
Nice to have
• I don't have an exact vision for how the poster should look, so I am totally open to you using your creativity to develop, arrange and present the content as you'd like.
• That said, I would like an image (photo or posterized image) of the person being quoted along with each quote. I do not have specific images that I would like you to use, so you will need to find the images on your own. The images don't need to be perfect... I am more interested in the poster relating the essence of the quotes and the people being quoted than I am in perfect photographic images of the people being quoted.

```html
<!DOCTYPE html>
<html lang="en">
<head>
<meta charset="utf-8">
<title>Learning Machines – Quote Poster</title>
<link href="https://fonts.googleapis.com/css2?family=Delius&display=swap" rel="stylesheet">
<style>
  :root{
    --ink:#111111;
    --paper:#ffffff;
    --night:#050505;
    --amber:#f4a81c;
    --violet:#a23ad9;
    --lime:#7fe12c;
    --crimson:#ee1c3e;
    --azure:#3a63d8;
    --tangerine:#f26a12;
    --leaf:#8fe236;
    --lilac:#a852d9;
    --photo-light:#cfcfcf;
    --photo-dark:#3a3a3a;
  }
  *{box-sizing:border-box;margin:0;padding:0}
  html,body{width:831px;height:1200px;overflow:hidden;background:var(--night)}
  .poster{
    position:relative;width:831px;height:1200px;overflow:hidden;
    background:var(--night);
    font-family:"Delius",cursive;
  }
  .splash-texture{
    position:absolute;inset:0;
    background:
      radial-gradient(circle at 96% 3%, rgba(127,225,44,.35), transparent 9%),
      radial-gradient(circle at 88% 12%, rgba(58,99,216,.35), transparent 8%),
      radial-gradient(circle at 3% 30%, rgba(242,106,18,.3), transparent 8%),
      radial-gradient(circle at 5% 50%, rgba(238,28,62,.35), transparent 9%),
      radial-gradient(circle at 95% 48%, rgba(242,106,18,.35), transparent 7%),
      radial-gradient(circle at 8% 70%, rgba(58,99,216,.3), transparent 9%),
      radial-gradient(circle at 96% 85%, rgba(127,225,44,.3), transparent 8%),
      radial-gradient(circle at 5% 95%, rgba(162,58,217,.3), transparent 9%),
      radial-gradient(circle at 40% 2%, rgba(238,28,62,.2), transparent 8%);
  }
  .band{position:absolute;z-index:1}
  .band--1{left:135px;top:73px;width:530px;height:104px;background:var(--amber);
    clip-path:polygon(2% 6%,100% 0,99% 94%,0 100%)}
  .band--2{left:150px;top:200px;width:590px;height:110px;background:var(--violet);
    clip-path:polygon(3% 12%,100% 0,98% 88%,0 100%)}
  .band--3{left:140px;top:308px;width:610px;height:200px;background:var(--lime);
    clip-path:polygon(0 4%,97% 0,100% 96%,2% 100%)}
  .band--4{left:70px;top:532px;width:600px;height:134px;background:var(--crimson);
    clip-path:polygon(1% 4%,100% 0,99% 100%,0 94%)}
  .band--5{left:40px;top:664px;width:680px;height:168px;background:var(--azure);
    clip-path:polygon(0 8%,100% 0,98% 94%,2% 100%)}
  .band--6{left:40px;top:832px;width:590px;height:110px;background:var(--tangerine);
    clip-path:polygon(2% 4%,100% 0,99% 100%,0 92%)}
  .band--7{left:165px;top:962px;width:580px;height:92px;background:var(--leaf);
    clip-path:polygon(0 10%,100% 0,98% 90%,3% 100%)}
  .band--8{left:175px;top:1078px;width:555px;height:88px;background:var(--lilac);
    clip-path:polygon(1% 6%,100% 0,100% 94%,0 100%)}

  .portrait{position:absolute;z-index:2;
    background:linear-gradient(160deg,var(--photo-light),var(--photo-dark))}
  .portrait--1{left:36px;top:42px;width:161px;height:185px}
  .portrait--2{left:598px;top:156px;width:160px;height:156px}
  .portrait--3{left:10px;top:306px;width:222px;height:193px}
  .portrait--4{left:640px;top:488px;width:129px;height:168px}
  .portrait--5{left:42px;top:603px;width:140px;height:188px}
  .portrait--6{left:640px;top:712px;width:150px;height:224px}
  .portrait--7{left:42px;top:894px;width:130px;height:156px}
  .portrait--8{left:648px;top:997px;width:126px;height:167px}

  .quote{position:absolute;z-index:3;font-size:18px;line-height:21px;color:var(--ink)}
  .quote--light{color:var(--paper);text-shadow:0 0 2px var(--ink),1px 1px 0 var(--ink)}
  .quote__text{display:block}
  .quote__name{display:block;margin-top:9px;font-size:17px;font-style:normal;color:var(--ink);text-shadow:none}
  .quote--right{text-align:right}

  .quote--1{left:208px;top:92px}
  .quote--1 .quote__name{margin-left:18px}
  .quote--2{left:165px;top:226px;width:415px;transform:rotate(-2deg)}
  .quote--2 .quote__name{margin-right:45px}
  .quote--3{left:250px;top:324px;width:470px;transform:rotate(3deg);line-height:19.5px}
  .quote--3 .quote__name{margin-top:8px;margin-left:30px}
  .quote--4{left:100px;top:560px;width:520px}
  .quote--4 .quote__name{margin-right:10px;margin-top:14px}
  .quote--5{left:198px;top:684px;width:500px;transform:rotate(-2deg)}
  .quote--5 .quote__name{margin-left:30px;margin-top:3px}
  .quote--6{left:55px;top:846px;width:560px;transform:rotate(-1deg)}
  .quote--6 .quote__name{margin-right:0;margin-top:6px}
  .quote--7{left:192px;top:978px;width:440px;transform:rotate(-2deg)}
  .quote--7 .quote__name{margin-left:40px;margin-top:18px}
  .quote--8{left:225px;top:1088px;width:395px}
  .quote--8 .quote__name{margin-right:10px;margin-top:6px}
</style>
</head>
<body>
<main class="poster">
  <div class="splash-texture" role="img" aria-label="Multicoloured paint splatter texture on black"></div>

  <div class="band band--1"></div>
  <div class="band band--2"></div>
  <div class="band band--3"></div>
  <div class="band band--4"></div>
  <div class="band band--5"></div>
  <div class="band band--6"></div>
  <div class="band band--7"></div>
  <div class="band band--8"></div>

  <div class="portrait portrait--1" role="img" aria-label="Black and white portrait of Dorian Fletcher"></div>
  <div class="portrait portrait--2" role="img" aria-label="Black and white portrait of Marcus Olden"></div>
  <div class="portrait portrait--3" role="img" aria-label="Black and white portrait of Frankie Dalgarth"></div>
  <div class="portrait portrait--4" role="img" aria-label="Black and white portrait of Kees R. T. Ter Haverkamp"></div>
  <div class="portrait portrait--5" role="img" aria-label="Black and white portrait of Rohan Kapadia"></div>
  <div class="portrait portrait--6" role="img" aria-label="Black and white portrait of Ned Yarrow"></div>
  <div class="portrait portrait--7" role="img" aria-label="Black and white portrait of Glenn Mosbacker"></div>
  <div class="portrait portrait--8" role="img" aria-label="Black and white portrait of Dieter Kolbach"></div>

  <blockquote class="quote quote--1">
    <span class="quote__text">You’re only given a little spark of madness.<br>You mustn’t lose it</span>
    <cite class="quote__name">Dorian Fletcher</cite>
  </blockquote>

  <blockquote class="quote quote--2 quote--right">
    <span class="quote__text">The most contrarian thing of all is not to<br>oppose the crowd but to think for yourself</span>
    <cite class="quote__name">Marcus Olden</cite>
  </blockquote>

  <blockquote class="quote quote--3 quote--light">
    <span class="quote__text">I constantly see people rise in life who are<br>not the smartest, sometimes not even the most<br>diligent, but they are learning machines.<br>They go to bed every night a little wiser than<br>they were when they got up and boy does that<br>help, particularly when you have a long run ahead<br>of you</span>
    <cite class="quote__name">Frankie Dalgarth</cite>
  </blockquote>

  <blockquote class="quote quote--4 quote--light quote--right">
    <span class="quote__text">In theory, there’s no difference between theory<br>and practice. But, in practice, there is</span>
    <cite class="quote__name">Kees R. T. Ter Haverkamp</cite>
  </blockquote>

  <blockquote class="quote quote--5 quote--light">
    <span class="quote__text">At the end of the day, a reactionary life is a normal life.<br>One thing is consistent in every remarkable person:<br>they decide to do something remarkable.<br>Don’t let the world choose who you become</span>
    <cite class="quote__name">Rohan Kapadia</cite>
  </blockquote>

  <blockquote class="quote quote--6 quote--light quote--right">
    <span class="quote__text">It usually takes 3-4 months to try enough that you can<br>do a proper 80/20 analysis, then two months to design<br>systems to scale what *is* working</span>
    <cite class="quote__name">Ned Yarrow</cite>
  </blockquote>

  <blockquote class="quote quote--7 quote--light">
    <span class="quote__text">Authority is 20 percent given, 80 percent taken</span>
    <cite class="quote__name">Glenn Mosbacker</cite>
  </blockquote>

  <blockquote class="quote quote--8 quote--light quote--right">
    <span class="quote__text">Your actions are consistent with the<br>way the world occurs to you</span>
    <cite class="quote__name">Dieter Kolbach</cite>
  </blockquote>
</main>
</body>
</html>
```